Brovenna a national investment company

We need a logo/letterhead design to describe our business. We use our business across the country to buy and sale property, buy property mineral rights, make investments in small businesses. Our business goal is to promotes integrity, security and growth in small investments. We want our product to reflect our goals.
Updates
I "think" I want a modern, sleek, not too busy design. I "think" I want a dark green and black/grey colors. However, y'all know best and I am looking forward to seeing your creativity in our design. Thanks for accepting our project. -Delphine
We are pleased with some of the designs submitted. We would like for the designs to reflect our company name as it appears on our license, Brovenna. We appreciate the designers who took into consideration our colors we specified. Thanks for all the hard work. We will make a decision tomorrow. You still have time to submit more ideas.
Industry/Entity Type
Investment
Logo Text
Brovenna LLC
Look and feel
Each slider illustrates characteristics of the customer's brand and the style your logo design should communicate.

```html
<!DOCTYPE html>
<html lang="en">
<head>
<meta charset="utf-8">
<title>Brovenna Letterhead</title>
<link href="https://fonts.googleapis.com/css2?family=Arimo:wght@400;700&display=swap" rel="stylesheet">
<style>
  :root {
    --backdrop: #ececec;
    --paper: #ffffff;
    --ink: #231f20;
    --accent: #e8731a;
    --band-text: #ffffff;
  }
  * { margin: 0; padding: 0; box-sizing: border-box; }
  html, body {
    width: 1200px;
    height: 943px;
    overflow: hidden;
    background: var(--backdrop);
    font-family: "Arimo", Arial, sans-serif;
  }
  .letterhead {
    position: absolute;
    left: 289px;
    top: 30px;
    width: 622px;
    height: 883px;
    background: var(--paper);
    box-shadow: 0 4px 18px rgba(0,0,0,0.12);
  }
  .brand {
    position: absolute;
    left: 44px;
    top: 48px;
  }
  .brand-row {
    display: flex;
    align-items: center;
    gap: 8px;
  }
  .brand-square {
    width: 26px;
    height: 26px;
    background: var(--ink);
  }
  .brand-name {
    color: var(--accent);
    font-weight: 700;
    font-size: 34px;
    line-height: 1;
    letter-spacing: -0.5px;
  }
  .brand-tagline {
    margin-top: 5px;
    color: var(--ink);
    font-size: 9.5px;
    letter-spacing: 0.2px;
  }
  .contact-band {
    position: absolute;
    left: 0;
    right: 0;
    bottom: 34px;
    height: 20px;
    background: var(--ink);
    display: flex;
    align-items: center;
    justify-content: flex-end;
    gap: 16px;
    padding: 0 36px;
  }
  .contact-item {
    display: flex;
    align-items: center;
    gap: 4px;
    color: var(--band-text);
    font-size: 9px;
    white-space: nowrap;
  }
  .contact-icon {
    width: 10px;
    height: 10px;
    flex: none;
  }
</style>
</head>
<body>
  <main class="letterhead">
    <header class="brand">
      <div class="brand-row">
        <span class="brand-square"></span>
        <span class="brand-name">Brovenna</span>
      </div>
      <p class="brand-tagline">A National Investment Company</p>
    </header>

    <footer class="contact-band">
      <span class="contact-item">
        <svg class="contact-icon" viewBox="0 0 10 10"><circle cx="5" cy="5" r="5" fill="#e8731a"/><path d="M5 2.2a1.8 1.8 0 0 0-1.8 1.8c0 1.4 1.8 3.6 1.8 3.6s1.8-2.2 1.8-3.6A1.8 1.8 0 0 0 5 2.2z" fill="#231f20"/><circle cx="5" cy="4" r="0.6" fill="#e8731a"/></svg>
        Address Here Address Here Address
      </span>
      <span class="contact-item">
        <svg class="contact-icon" viewBox="0 0 10 10"><circle cx="5" cy="5" r="5" fill="#e8731a"/><path d="M3.3 2.6l1 1-.5.7c.3.7.8 1.2 1.5 1.5l.7-.5 1 1-.6.9C4.7 7 3 5.3 2.4 3.2z" fill="#231f20"/></svg>
        02 5550 1847
      </span>
      <span class="contact-item">
        <svg class="contact-icon" viewBox="0 0 10 10"><circle cx="5" cy="5" r="5" fill="#e8731a"/><rect x="2.5" y="3.2" width="5" height="3.6" fill="none" stroke="#231f20" stroke-width="0.7"/><path d="M2.5 3.2L5 5.2l2.5-2" fill="none" stroke="#231f20" stroke-width="0.7"/></svg>
        info@brovenna.com
      </span>
      <span class="contact-item">
        <svg class="contact-icon" viewBox="0 0 10 10"><circle cx="5" cy="5" r="5" fill="#e8731a"/><circle cx="5" cy="5" r="2.6" fill="none" stroke="#231f20" stroke-width="0.6"/><path d="M2.4 5h5.2M5 2.4c-1.2 1.4-1.2 3.8 0 5.2M5 2.4c1.2 1.4 1.2 3.8 0 5.2" fill="none" stroke="#231f20" stroke-width="0.5"/></svg>
        www.brovenna.com
      </span>
    </footer>
  </main>
</body>
</html>
```